Web design for facial expression recognition service

We offer a service which allows customers to film large panels of participants looking at some video/screen (e.g. an advertisement) and to analyze the facial expressions shown by the participants. We are looking for the design of a new website which will make it easy for our customers to setup and view the results of these experiments online.
Competitor's websites that may serve as a reference are:
http://www.moriventa.com/quelbo/#pane_overview
http://www.dunvarpix.com/homepage.aspx
https://www.tamlora.com/
The website will (for as far as the design is concerned) consist of three parts:
- A public home page (and perhaps some contact/news/about page), designed to catch the attention/interest potential customers.
- A (protected) project result page, showing the results in an interactive page with charts and numerical data.
- Pages (also protected) with fields and tables (setting up the project details).
The winner of this design project should provide us with at least one design for each of the above in order to get a complete 'theme' going which our developers can use. However, you are welcome to initially only provide the design for the project result page and/or home page.
We are looking for a modern, fresh, yet professional look (my client is a more established party in the field).
The final delivery should consist of layered Photoshop or Illustrator files.
Thank you in advance for participating!
Updates
Dear designers,
Project Deadline Extended
Reason: Extending the deadline by a few days to give designers a chance to submit designs for the other pages and process further feedback.
Target Market(s)
marketing research agencies (B2B service)
Requirements
Must have
- Home page:
- Basic advertisement of the service; some quick explanation of how it works
- A way to login for existing users
- A link/button/banner inviting people to sign up
- Navigation controls to 2-3 other pages
- Social media links (Facebook, LinkedIn group)
- Company logo (sorry, can't provide it as my client wishes to remain anonymous for now, but it's rounded and has blue as it's main color).
- Copyright / creator details
Project result page:
(see attachment 1 for a functional mockup - the design may follow this layout closely, or be completely different)
- Title
- A video player and basic numerical data
- Different views of the analysis results can dynamically be added/removed/collapsed/expanded; each one of these views will show some kind of chart, filters (combos), numerical data and a download button/link.
- A way to sign out, go to the main project page and go to the main page
- Logo
- Copyright
The form pages:
(see attachment 2 for a functional mockup of one of the pages; feel free to change some elements to better show the overall style)
- Title
- Text fields, combos, calendar pickers, tables, navigation links
- Logo
- Copyright
Nice to have
- Any creative text elements or product logo/symbol are a bonus. However, the basic "Lorem Ipsum" would do too.

```html
<!DOCTYPE html>
<html lang="en">
<head>
<meta charset="utf-8">
<title>Vellanhorst – Facial Expression Analysis</title>
<link href="https://fonts.googleapis.com/css2?family=PT+Sans:ital,wght@0,400;0,700;1,400;1,700&display=swap" rel="stylesheet">
<style>
:root{
  --blue:#1a74c4;
  --blue-dark:#0d4f8e;
  --blue-light:#47a8e4;
  --sky:#3a9ee0;
  --topbar:#2b2b2b;
  --grey-bar:#8e9298;
  --row:#e6e6e6;
  --row-alt:#efefef;
  --text:#444;
  --link:#1b6fb8;
  --green:#8bc21b;
  --white:#fff;
}
*{box-sizing:border-box;margin:0;padding:0}
html,body{width:783px;height:1200px;overflow:hidden;background:#fff}
body{position:relative;font-family:"PT Sans",Arial,sans-serif;color:var(--text)}
.abs{position:absolute}
.topbar{left:0;top:0;width:783px;height:28px;background:linear-gradient(#3a3a3a,#222)}
.util{top:9px;font-size:7px;line-height:9px;color:#bbb;white-space:nowrap}
.login{left:616px;top:5px;width:48px;height:18px;border-radius:3px;background:#1a1a1a;color:#ddd;font-size:8px;padding:4px 8px}
.login::after{content:"";position:absolute;right:6px;top:5px;width:7px;height:7px;border-radius:50%;background:#eee}
.hero{left:0;top:28px;width:783px;height:294px;background:linear-gradient(180deg,#0f5ea8 0%,#1a74c4 60%,#3c9fe0 100%)}
.brand{left:118px;top:58px;font-size:20px;font-weight:700;color:var(--white);display:flex;align-items:center;gap:6px}
.brand i{width:12px;height:12px;border-radius:50%;background:#37c4f2;display:block}
.nav{top:40px;font-size:8px;font-weight:700;color:#fff;white-space:nowrap;transform:translateX(-50%);padding:4px 0}
.nav.on{background:linear-gradient(#2f87d2,#125fa6);border:1px solid #8fc4ee;border-radius:5px;width:42px;text-align:center}
.headline{left:118px;top:118px;font-style:italic;font-weight:700;font-size:20px;line-height:20px;color:#fff;letter-spacing:-.5px}
.sub{left:118px;top:167px;font-style:italic;font-size:12px;line-height:16px;color:#fff;letter-spacing:-.3px}
.blurb{left:118px;top:206px;width:260px;font-size:5.6px;line-height:10px;color:#fff}
.signup{left:122px;top:259px;width:120px;height:22px;border-radius:11px;background:linear-gradient(#b6e44a,#6fa80f);border:1px solid #d8f59a;box-shadow:0 3px 10px rgba(160,230,50,.6);font-size:10px;font-weight:700;color:#2d4a05;padding:4px 15px;white-space:nowrap}
.screen{left:395px;top:87px;width:270px;height:170px;background:#111;border:2px solid #ddd;border-radius:4px;padding:8px}
.screen div{width:100%;height:100%;background:linear-gradient(135deg,#e8cfb0,#c9a37f 50%,#f0dfc0)}
.stand{left:495px;top:257px;width:70px;height:46px;background:linear-gradient(#eee,#aaa);clip-path:polygon(22% 0,78% 0,70% 70%,100% 100%,0 100%,30% 70%)}
.dots{left:628px;top:307px;display:flex;gap:3px}
.dots i{width:6px;height:6px;border-radius:50%;background:#7aa6c8}
.dots i:first-child{background:#3cb6f2}
.photo{left:118px;top:342px;width:274px;height:166px;border:2px solid #e5e5e5;background:linear-gradient(120deg,#d9b59b,#b58463 45%,#e8ded5)}
.proj-title{left:416px;top:342px;width:249px;height:33px;background:linear-gradient(#fff,#e1e1e1);font-style:italic;font-weight:700;font-size:15px;color:var(--link);padding:8px 15px}
.avatar{left:417px;top:387px;width:78px;height:70px;border:2px solid #ddd;background:linear-gradient(#9bb3c8,#b3896a)}
.fields{left:510px;top:391px;font-size:7px;line-height:14.5px;color:#555}
.fields b{font-weight:400;color:var(--link)}
.about{left:417px;top:463px;width:250px;font-size:5.6px;line-height:10px;color:#555}
.about h3{font-size:8px;color:var(--link);font-weight:400;margin-bottom:1px}
.panel{left:144px;width:520px;border:1px solid #ddd;box-shadow:0 0 3px rgba(0,0,0,.12);background:#fff}
.icons{display:flex;flex-direction:column;gap:4px}
.icons i{width:12px;height:12px;border-radius:50%;display:block;border:1px solid #bbb}
.i-x{background:#2f9a2f}.i-m{background:#d22}.i-a{background:#2a6fbf}
.filterbar{width:290px;height:24px;background:linear-gradient(#2a86d1,#125fa6);display:flex;gap:12px;padding:3px 8px}
.filterbar span,.tab span{flex:1;background:linear-gradient(#a2a6ab,#7b7f85);color:#fff;font-size:6.5px;text-align:center;padding:4px 0;border-radius:2px;white-space:nowrap}
.statshead{width:172px;height:24px;background:linear-gradient(#2a86d1,#125fa6);color:#fff;font-size:10px;padding:6px 12px}
.stats{border-collapse:separate;border-spacing:1px;width:174px;font-size:6.2px;color:#555}
.stats th{background:#aaa;color:#fff;font-weight:400;height:14px}
.stats th:first-child{width:71px}
.stats td{background:var(--row);height:15.3px;padding-left:8px}
.stats td+td{background:var(--row-alt)}
.chart text{font-family:"PT Sans",Arial,sans-serif;font-size:6px;fill:#999}
.opt-title{font-size:8px;color:var(--link)}
.tab{width:229px;height:24px;background:linear-gradient(#2a86d1,#125fa6);display:flex;gap:15px;padding:3px 5px}
.form{width:229px;background:var(--row-alt);font-size:6.3px;color:#555}
.form .r{display:flex;height:26px;align-items:center;border-bottom:1px solid #fff}
.form .l{width:100px;text-align:right;padding-right:10px;line-height:8px}
.sel{height:12px;border:1px solid #ccc;background:#fff;font-size:5.5px;color:#999;padding:2px 4px;position:relative;margin-left:6px;white-space:nowrap;overflow:hidden}
.sel::after{content:"";position:absolute;right:1px;top:1px;width:8px;height:8px;background:#ddd;border:1px solid #999}
.footer{left:0;top:1151px;width:783px;height:49px;background:linear-gradient(#1366b2,#0c4f8f)}
.fnav{left:118px;top:1164px;font-size:6px;color:#fff;word-spacing:3px}
.copy{left:118px;top:1178px;font-size:6px;color:#fff}
.copy span{color:#6cc4f5}
.social{left:575px;top:1165px;font-size:6px;color:#fff;text-align:right;line-height:10px}
.sq{top:1166px;width:14px;height:14px;background:#5b87c4;border-radius:2px}
</style>
</head>
<body>
<div class="abs topbar"></div>
<span class="abs util" style="left:489px">Home</span>
<span class="abs util" style="left:522px">|</span>
<span class="abs util" style="left:539px">Help</span>
<span class="abs util" style="left:569px">|</span>
<span class="abs util" style="left:586px">Sitemap</span>
<div class="abs login">Login</div>

<header class="abs hero"></header>
<div class="abs brand">Vellanhorst<i></i></div>
<a class="abs nav on" style="left:331px">Home</a>
<a class="abs nav" style="left:393px">About Us</a>
<a class="abs nav" style="left:455px">Team</a>
<a class="abs nav" style="left:513px">Videos</a>
<a class="abs nav" style="left:573px">Clients</a>
<a class="abs nav" style="left:641px">Contact Us</a>
<h1 class="abs headline">We are a facial recognition<br>analysis company</h1>
<p class="abs sub">We make group of 10 users see a video and analyse<br>their facial expressions</p>
<p class="abs blurb">Lorem Ipsum is simply dummy text of the printing and typesetting industry. Lorem Ipsum has been the industry's standard dummy text ever since the 1500s, when an unknown printer took a galley of type and scrambled it to make a type specimen book.</p>
<div class="abs signup">People to Signup ↓</div>
<div class="abs screen"><div role="img" aria-label="Portrait photo with facial analysis grid lines"></div></div>
<div class="abs stand"></div>
<div class="abs dots"><i></i><i></i><i></i><i></i></div>

<div class="abs photo" role="img" aria-label="Photo of a participant's face with measurement guide lines"></div>
<h2 class="abs proj-title">Project information</h2>
<div class="abs avatar" role="img" aria-label="Profile photo of the project contact"></div>
<div class="abs fields"><b>Name :</b> Joren Maltby<br><b>Email :</b> joren@velnio.com<br><b>Destination :</b> Designer</div>
<div class="abs about"><h3>About Project</h3>Lorem Ipsum is simply dummy text of the printing and typesetting industry. Lorem Ipsum has been the industry's standard dummy text ever since the 1500s, when an unknown printer took a galley of type and scrambled it to make a type specimen book.</div>

<section class="abs panel" style="top:529px;height:176px"></section>
<div class="abs icons" style="left:147px;top:535px"><i class="i-x"></i><i class="i-m"></i><i class="i-a"></i></div>
<div class="abs filterbar" style="left:181px;top:538px"><span>Stimulus 1 ⌄</span><span>Age 3 - 50 ⌄</span><span>Male ⌄</span></div>
<div class="abs statshead" style="left:483px;top:537px">Statistics</div>
<table class="abs stats" style="left:482px;top:567px">
<tr><th></th><th>Mean</th><th>St.dev</th></tr>
<tr><td>Neutral</td><td></td><td></td></tr><tr><td>Happy</td><td></td><td></td></tr><tr><td>Sad</td><td></td><td></td></tr><tr><td>Angry</td><td></td><td></td></tr><tr><td>Surprised</td><td></td><td></td></tr><tr><td>Scared</td><td></td><td></td></tr><tr><td>Digusted</td><td></td><td></td></tr>
</table>
<svg class="abs chart" style="left:175px;top:590px" width="270" height="96" viewBox="0 0 270 96">
<rect x="12" y="8" width="14" height="7" fill="#2a9ee0"/><text x="30" y="14" style="fill:#333;font-weight:700">Lorem</text>
<rect x="12" y="19" width="14" height="7" fill="#bfe2f7"/><text x="30" y="25" style="fill:#333;font-weight:700">Ipsum</text>
<line x1="10" y1="78" x2="256" y2="78" stroke="#ccc"/>
<polyline fill="none" stroke="#2a9ee0" points="10,50 32,59 55,58 76,49 99,39 121,36 143,48 165,43 187,31 209,40 231,33 254,17"/>
<polyline fill="none" stroke="#a9d6f3" points="10,60 32,52 55,52 76,44 99,60 121,52 143,44 165,36 187,52 209,42 231,28 254,26"/>
<g fill="#2a9ee0"><circle cx="10" cy="50" r="1.6"/><circle cx="32" cy="59" r="1.6"/><circle cx="55" cy="58" r="1.6"/><circle cx="76" cy="49" r="1.6"/><circle cx="99" cy="39" r="1.6"/><circle cx="121" cy="36" r="1.6"/><circle cx="143" cy="48" r="1.6"/><circle cx="165" cy="43" r="1.6"/><circle cx="187" cy="31" r="1.6"/><circle cx="209" cy="40" r="1.6"/><circle cx="231" cy="33" r="1.6"/><circle cx="254" cy="17" r="1.6"/></g>
<g text-anchor="middle"><text x="12" y="91">Jan</text><text x="32" y="91">Feb</text><text x="55" y="91">Mar</text><text x="76" y="91">Apr</text><text x="99" y="91">May</text><text x="121" y="91">Jun</text><text x="143" y="91">Jul</text><text x="165" y="91">Aug</text><text x="187" y="91">Sep</text><text x="209" y="91">Nov</text><text x="231" y="91">Oct</text><text x="254" y="91">Dec</text></g>
</svg>

<section class="abs panel" style="top:718px;height:175px"></section>
<div class="abs icons" style="left:147px;top:724px"><i class="i-x"></i><i class="i-m"></i><i class="i-a"></i></div>
<div class="abs filterbar" style="left:181px;top:727px"><span>Stimulus 1 ⌄</span><span>Age 9 - 21 ⌄</span><span>Male ⌄</span></div>
<div class="abs statshead" style="left:483px;top:726px">Statistics</div>
<table class="abs stats" style="left:482px;top:755px">
<tr><th></th><th>Mean</th><th>St.dev</th></tr>
<tr><td>Neutral</td><td></td><td></td></tr><tr><td>Happy</td><td></td><td></td></tr><tr><td>Sad</td><td></td><td></td></tr><tr><td>Angry</td><td></td><td></td></tr><tr><td>Surprised</td><td></td><td></td></tr><tr><td>Scared</td><td></td><td></td></tr><tr><td>Digusted</td><td></td><td></td></tr>
</table>
<svg class="abs chart" style="left:175px;top:770px" width="270" height="115" viewBox="0 0 270 115">
<g text-anchor="end"><text x="18" y="12">100</text><text x="18" y="35">75</text><text x="18" y="57">50</text><text x="18" y="80">25</text><text x="18" y="102">0</text></g>
<g stroke="#eee"><line x1="24" y1="10" x2="260" y2="10"/><line x1="24" y1="33" x2="260" y2="33"/><line x1="24" y1="55" x2="260" y2="55"/><line x1="24" y1="78" x2="260" y2="78"/></g>
<line x1="24" y1="6" x2="24" y2="100" stroke="#bbb"/><line x1="24" y1="100" x2="260" y2="100" stroke="#bbb"/>
<g fill="#6fb4de" stroke="#4d98c8" stroke-width=".6">
<rect x="32" y="43" width="19" height="56" rx="2"/><rect x="61" y="34" width="19" height="65" rx="2"/><rect x="88" y="63" width="19" height="36" rx="2"/><rect x="117" y="24" width="19" height="75" rx="2"/><rect x="145" y="16" width="19" height="83" rx="2"/><rect x="176" y="24" width="19" height="75" rx="2"/><rect x="201" y="20" width="19" height="79" rx="2"/><rect x="229" y="56" width="19" height="43" rx="2"/>
</g>
<g text-anchor="middle"><text x="42" y="112">Lorem</text><text x="71" y="112">Lorem</text><text x="98" y="112">Lorem</text><text x="127" y="112">Lorem</text><text x="155" y="112">Lorem</text><text x="186" y="112">Lorem</text><text x="211" y="112">Lorem</text><text x="239" y="112">Lorem</text></g>
</svg>

<section class="abs panel" style="top:908px;height:227px"></section>
<div class="abs icons" style="left:147px;top:915px"><i class="i-x"></i></div>
<div class="abs opt-title" style="left:181px;top:916px">Add new chart Options</div>
<div class="abs tab" style="left:181px;top:933px"><span>Variable</span><span>Options</span></div>
<div class="abs form" style="left:181px;top:965px"><div class="r"><div class="l">Stimulus<br>Information type</div><div class="sel" style="width:104px">Comparison</div></div></div>

<div class="abs opt-title" style="left:181px;top:1000px">2.a Information Type = Single</div>
<div class="abs tab" style="left:181px;top:1017px"><span>Variable</span><span>Options</span></div>
<div class="abs form" style="left:181px;top:1049px">
<div class="r"><div class="l">Stimulus<br>Information type</div><div class="sel" style="width:104px">Statistics Table</div></div>
<div class="r"><div class="l">Graph Data</div><div class="sel" style="width:104px">Expressions</div></div>
<div class="r"><div class="l">Gender<br>Age Range</div><div class="sel" style="width:52px">Age Min</div><div class="sel" style="width:48px">Age Max</div></div>
</div>

<div class="abs opt-title" style="left:427px;top:1000px">3.a Information Type = Comparison</div>
<div class="abs tab" style="left:427px;top:1017px"><span>Variable</span><span>Options</span></div>
<div class="abs form" style="left:427px;top:1049px">
<div class="r"><div class="l">Graph Type</div><div class="sel" style="width:104px">Statistics Table</div></div>
<div class="r"><div class="l">Graph Data</div><div class="sel" style="width:104px">Expressions</div></div>
<div class="r"><div class="l">Comparison</div><div class="sel" style="width:104px">Male vs Female</div></div>
</div>

<footer class="abs footer"></footer>
<div class="abs fnav">Home | About Us | Team | Videos | Clients | Contact Us</div>
<div class="abs copy">Copyright ©2013. <span>Vellanhorst.</span> All rights reserved.</div>
<div class="abs social">Connect to<br>our Social Network :</div>
<div class="abs sq" style="left:633px"></div>
<div class="abs sq" style="left:651px"></div>
</body>
</html>
```